Letter design, envelope design, and more

Hello, we the Tavrin Gmbh are looking for our shop. Letter C5. Design does not have to be like a business card, so it can have straight lines. Only the color is important. The logo is the text under TaVRin omit.It should not be playful but Profesionel

Font styles to use
Sans Serif

Colors
0555a3
3176b5
85abd2
85cae6
34a7d8
0792cd
cee9f5
cfdfed
000000

Requirements
Must have
• Color like business card, Please, with the text under TaVRin, Correct address Lindmattstr. 4 Zip code 9517 Sarnegg, as well as Couvert Without addressing only design and logo with TaVrn
Nice to have
• more writing articles
Should not have
• Not too colored, Text under TaVRin, bright colors

```html
<!DOCTYPE html>
<html lang="en">
<head>
<meta charset="utf-8">
<title>Tavrin Gmbh – Letterhead and Envelope</title>
<link href="https://fonts.googleapis.com/css2?family=Lato:wght@400;700&family=Kaushan+Script&display=swap" rel="stylesheet">
<style>
  :root {
    --stage: #c9cacc;
    --paper: #ffffff;
    --navy: #232a6e;
    --steel: #7f9bb5;
    --rule: #8aa2b9;
    --body: #454545;
    --shadow: rgba(0,0,0,0.12);
  }
  * { margin: 0; padding: 0; box-sizing: border-box; }
  html, body { width: 1200px; height: 703px; overflow: hidden; }
  body {
    background: var(--stage);
    font-family: "Lato", Arial, sans-serif;
    position: relative;
  }

  /* ---------- Brand lockup ---------- */
  .brand { position: absolute; display: flex; align-items: center; color: var(--navy); }
  .brand-square { background: var(--navy); flex: none; }
  .brand-name { font-weight: 700; letter-spacing: 0.04em; line-height: 1; white-space: nowrap; }

  /* ---------- Letterhead ---------- */
  .letter {
    position: absolute; left: 52px; top: 56px; width: 429px; height: 602px;
    background: var(--paper); box-shadow: 0 0 2px var(--shadow);
  }
  .letter .brand { left: 25px; top: 22px; gap: 8px; }
  .letter .brand-square { width: 26px; height: 26px; }
  .letter .brand-name { font-size: 24px; }

  .web-rule { position: absolute; left: 0; right: 0; top: 68px; height: 2px; }
  .web-rule .line { position: absolute; top: 0; height: 2px; background: var(--rule); }
  .web-rule .line.left { left: 0; width: 298px; }
  .web-rule .line.right { left: 410px; width: 19px; }
  .web-address {
    position: absolute; font-size: 10px; letter-spacing: 0.2em; color: #3c3c3c; white-space: nowrap;
  }
  .web-address .domain { color: var(--steel); font-weight: 700; }
  .letter .web-address { left: 308px; top: -6px; }

  .letter-body { position: absolute; left: 24px; top: 98px; width: 386px; }
  .salutation { font-size: 10.5px; font-weight: 700; color: var(--navy); margin-bottom: 5px; }
  .letter-body p.copy {
    font-size: 8.15px; line-height: 12.9px; color: var(--body); margin-bottom: 11px;
    letter-spacing: 0.05px;
  }
  .closing { position: absolute; left: 24px; top: 468px; }
  .closing .phrase { font-size: 13px; color: #444; }
  .closing .signature {
    font-family: "Kaushan Script", cursive; font-size: 23px; color: var(--navy); margin-top: 0;
  }

  .contact-bar {
    position: absolute; left: 0; right: 0; top: 582px;
    display: flex; justify-content: center; align-items: center;
    font-size: 8px; color: #333;
  }
  .contact-item { display: flex; align-items: center; gap: 3px; padding: 0 8px; }
  .contact-item + .contact-item { border-left: 1px solid #b8b8b8; }
  .contact-item svg { width: 8px; height: 8px; }

  /* ---------- Envelope ---------- */
  .envelope-flap { position: absolute; left: 534px; top: 90px; width: 603px; height: 106px; }
  .envelope {
    position: absolute; left: 534px; top: 195px; width: 603px; height: 429px;
    background: var(--paper); box-shadow: 0 0 2px var(--shadow);
  }
  .envelope .brand { left: 31px; top: 30px; gap: 10px; }
  .envelope .brand-square { width: 30px; height: 30px; }
  .envelope .brand-name { font-size: 28px; }
  .envelope .web-rule { top: 407px; }
  .envelope .web-rule .line.left { width: 240px; }
  .envelope .web-rule .line.right { left: 363px; width: 240px; }
  .envelope .web-address { left: 250px; top: -8px; font-size: 11px; }
</style>
</head>
<body>

  <!-- Letterhead -->
  <section class="letter">
    <div class="brand">
      <span class="brand-square"></span>
      <span class="brand-name">TAVRIN GMBH</span>
    </div>

    <div class="web-rule">
      <span class="line left"></span>
      <span class="web-address">www.<span class="domain">tavrin</span>.ch</span>
      <span class="line right"></span>
    </div>

    <div class="letter-body">
      <p class="salutation">Dear Mr. Lorem,</p>
      <p class="copy">Lorem ipsum dolor sit amet, consectetuer adipiscing elit, sed diam nonummy nibh euismod tincidunt ut laoreet dolore magna aliquam erat volutpat. Ut wisi enim ad minim veniam, quis nostrud exerci tation ullamcorper suscipit lobortis nisl ut aliquip ex ea commodo consequat. Duis autem vel eum iriure dolor in hendiusto odio dignissim qui blandit praesent luptatum zzril delenit.facilisi.</p>
      <p class="copy">Lorem ipsum dolor sit amet, consectetuer adipiscing elit, sed diam nonummy nibh euismod tincidunt ut laoreet dolore magna aliquam erat volutpat. Ut wisi enim ad minim veniam, quis nostrud exerci tation ullamcorper suscipit lobortis nisl ut aliquip ex ea commodo consequat.</p>
      <p class="copy">Lorem ipsum dolor sit amet, consectetuer adipiscing elit, sed diam nonummy nibh euismod tincidunt ut laoreet dolore magna aliquam erat volutpat. Ut wisi enim ad minim veniam, quis nostrud exerci tation ullamcorper suscipit lobortis nisl ut aliquip ex ea commodo consequat. Duis autem vel eum iriure dolor in hendiusto odio dignissim qui blandit praesent luptatum zzril delenit.facilisi.</p>
      <p class="copy">Lorem ipsum dolor sit amet, consectetuer adipiscing elit, sed diam nonummy nibh euismod tincidunt ut laoreet dolore magna aliquam erat volutpat. Ut wisi enim ad minim veniam, quis nostrud exerci tation ullamcorper suscipit lobortis nisl ut aliquip ex ea commodo consequat.</p>
      <p class="copy">Lorem ipsum dolor sit amet, consectetuer adipiscing elit, sed diam nonummy nibh euismod tincidunt ut laoreet dolore magna aliquam erat volutpat. Ut wisi enim ad minim veniam, quis nostrud exerci tation ullamcorper suscipit lobortis nisl ut aliquip ex ea commodo consequat. Duis autem vel eum iriure dolor in hendiusto odio dignissim qui blandit praesent luptatum zzril delenit.facilisi.</p>
      <p class="copy">Lorem ipsum dolor sit amet, consectetuer adipiscing elit, sed diam nonummy nibh euismod tincidunt ut laoreet dolore magna aliquam erat volutpat. Ut wisi enim ad minim veniam, quis nostrud exerci tation ullamcorper suscipit lobortis nisl ut aliquip ex ea commodo consequat.</p>
    </div>

    <div class="closing">
      <p class="phrase">Sincerely Your,</p>
      <p class="signature">Your Name</p>
    </div>

    <div class="contact-bar">
      <span class="contact-item">
        <svg viewBox="0 0 10 10" aria-hidden="true"><path d="M5 0.8a3.3 3.3 0 0 0-3.3 3.3C1.7 6.6 5 9.4 5 9.4s3.3-2.8 3.3-5.3A3.3 3.3 0 0 0 5 0.8z" fill="none" stroke="#333" stroke-width="1"/><circle cx="5" cy="4.1" r="1.2" fill="#333"/></svg>
        Lindmattstr. 4, 9517 Sarnegg
      </span>
      <span class="contact-item">
        <svg viewBox="0 0 10 10" aria-hidden="true"><circle cx="5" cy="5" r="4.3" fill="none" stroke="#333" stroke-width="0.9"/><path d="M3.6 2.8l1 1.1-0.5 0.7c0.3 0.6 0.8 1.1 1.4 1.4l0.7-0.5 1.1 1-0.6 0.8C5.2 7.2 2.8 4.8 2.8 3.4z" fill="#333"/></svg>
        +41 71 555 02 48
      </span>
      <span class="contact-item">
        <svg viewBox="0 0 10 10" aria-hidden="true"><rect x="1" y="2.5" width="8" height="5.5" fill="#333"/><path d="M1 2.5l4 3 4-3" fill="none" stroke="#fff" stroke-width="0.8"/></svg>
        info@tavrin.ch
      </span>
    </div>
  </section>

  <!-- Envelope -->
  <svg class="envelope-flap" viewBox="0 0 603 106" aria-hidden="true">
    <path d="M0 106 C4 80 10 64 42 56 L282 5 Q301 0 320 5 L561 56 C593 64 599 80 603 106 Z" fill="#7f9bb5"/>
  </svg>
  <section class="envelope">
    <div class="brand">
      <span class="brand-square"></span>
      <span class="brand-name">TAVRIN GMBH</span>
    </div>
    <div class="web-rule">
      <span class="line left"></span>
      <span class="web-address">www.<span class="domain">tavrin</span>.ch</span>
      <span class="line right"></span>
    </div>
  </section>

</body>
</html>
```